Leading Financial Advisory Firm Needs a Web Redesign

Job Type
Web Redesign

Task Outline
Create an Updated Web Design for our existing web site

Task Description
Dunmore Kestrel Group Inc. is a leading financial advisory firm to the global steel, metals and mining sectors. We are seeking a web designer to refashion, freshen and update the look of our existing website. The substance of the revised website should reflect our updated Credentials attached.

Our existing web site has an outdated “look”; it was originally put together quickly from an earlier PowerPoint presentation of our Credentials. We do not want the revised web site to look like a PowerPoint presentation which has been put up online. Rather, with a designer’s help, we would like to refashion the pages so that the look and feel of the site is consistent with a professional service organization's site. We are not interested in any significant changes in substance, just in format. There should also be no changes to the design/font/color of the “Dunmore Kestrel” logo.

The final selected designer will be responsible for all design and coding/programming responsibilities subject to our approval. The revised site should be done in Word Press or similar "user-friendly" application so that we can make edits afterwards.

A few specific changes:
• Textual changes:
• Wherever it currently says Dunmore Kestrel is an “affiliate” of Orvanne, this should be replaced with “Broker Dealer related services provided through Orvanne Partners LLC”; this appears on the copyright info on the bottom of each page;
• Please also add this telephone number to the 212 number listed: 917-555-0183;
• The text on the “About Us” tab needs to be updated as follows: “We currently have active steel, metals and mining assignments in Europe, South Africa, Australia and Ukraine.”
• The Services tab under Core Services currently says “Capital Raising (through affiliates)”; it should say “Capital Raising (through broker dealers)”;
• Our firm name in the Contacts tab should be “Dunmore Kestrel Group Inc.”
• Tara Wendle’ bio should be removed from the Bios tab;
• The map in the Global Scope and Perspective tab should be replaced with the map in the attached updated Credentials (see slide 11)

Very truly yours,

Dunmore Kestrel Group Inc.

Our current website is: http://www.dunmorekestrel.example

Deadline
5 Days

Target Market(s)
Companies in the steel, metals and mining sectors interested in financial advisory services and/or strategic and/or financial partners.

Industry/Entity Type

Financial

```html
<!DOCTYPE html>
<html lang="en">
<head>
<meta charset="utf-8">
<title>Dunmore Kestrel</title>
<link href="https://fonts.googleapis.com/css2?family=Open+Sans:wght@400;600&display=swap" rel="stylesheet">
<style>
:root{
  --green:#17670f;
  --green-dark:#0f5509;
  --text:#333;
  --muted:#777;
  --line:#dde3e8;
  --card-border:#d7dde2;
  --panel:#f4f5f6;
  --white:#fff;
}
*{box-sizing:border-box;margin:0;padding:0}
html,body{width:704px;height:1200px;overflow:hidden}
body{font-family:'Open Sans',sans-serif;color:var(--text);background:var(--white);position:relative}
.abs{position:absolute}
.topline{left:0;top:0;width:704px;height:2px;background:var(--green)}
.brand{left:77px;top:19px;display:flex;align-items:center;gap:6px}
.brand-mark{width:12px;height:12px;background:var(--green)}
.brand-name{font-weight:600;font-size:16px;color:var(--green);line-height:18px}
.call{left:566px;top:14px;font-size:10px;color:#777;line-height:14px}
.call b{display:block;font-weight:400;color:var(--green);font-size:10.5px}
.nav{left:0;top:53px;width:704px;height:30px;background:var(--green);border-bottom:2px solid var(--green-dark)}
.nav ul{list-style:none;display:flex;margin-left:77px;height:30px}
.nav li{color:#fff;font-size:10px;line-height:30px;padding:0 10px;border-left:1px solid #0e4e08;border-right:1px solid #2a7c20}
.nav li:first-child{padding-left:14px;padding-right:14px}
.hero{left:0;top:86px;width:704px;height:263px;background:linear-gradient(180deg,#6f9fd6 0%,#9ec0e6 35%,#b6b4ad 70%,#7f7a73 100%)}
.quote{left:77px;top:178px;width:317px;height:79px;background:#474747;color:#fff;font-size:14px;line-height:27px;text-align:center;padding-top:12px}
.card{top:372px;width:127px;height:159px;border:1px solid var(--card-border);box-shadow:0 2px 0 #e6eaed;text-align:center}
.card h3{font-weight:400;font-size:10px;color:var(--green);margin-top:12px}
.card svg{display:block;margin:10px auto 0}
.card p{font-size:6px;line-height:11px;color:#666;text-align:left;padding:0 12px 0 14px;margin-top:10px;letter-spacing:-.1px}
.card a{display:block;text-align:left;padding:0 16px;font-size:7px;color:var(--green);margin-top:7px;text-decoration:none}
.heading{font-size:10.5px;color:var(--green);display:flex;align-items:center;font-weight:400}
.heading::after{content:"";flex:1;height:1px;background:var(--line);margin-left:8px;order:1}
.arrows{display:flex;gap:2px;margin-left:8px;order:2}
.arrows span{width:12px;height:11px;background:#eceeef;border:1px solid #ddd;font-size:6px;line-height:9px;text-align:center;color:#888}
.about p{font-size:6.5px;line-height:12px;color:#777;margin-top:20px}
.about p+p{margin-top:12px}
.testi-box{left:461px;top:590px;width:166px;height:61px;border:1px solid var(--card-border);font-size:6.5px;line-height:11.5px;color:#888;font-style:italic;padding:11px 16px}
.testi-person{left:461px;top:659px;width:166px;height:31px;background:var(--panel);text-align:right;padding:5px 36px 0 0}
.testi-person b{display:block;font-weight:600;color:var(--green);font-size:9px;line-height:11px}
.testi-person span{font-size:6.5px;color:#777}
.portrait{left:599px;top:660px;width:24px;height:29px;background:linear-gradient(#cfc7bf,#6c6560)}
.post{top:754px;width:173px;height:160px;background:var(--panel);border-bottom:2px solid #e2e6e9;text-align:center}
.post .photo{width:173px;height:121px}
.post .date{left:118px;top:93px;width:27px;height:28px;background:var(--green);color:#fff;font-size:6px;line-height:8px;padding-top:4px}
.post .date b{display:block;font-weight:400;font-size:11px;line-height:12px}
.post .media{left:145px;top:93px;width:28px;height:28px;background:#5e5e5e}
.post h4{font-weight:400;font-size:8px;color:var(--green);margin-top:9px}
.post p{font-size:6.5px;color:#555;margin-top:5px}
.banner{left:77px;top:954px;width:550px;height:44px;background:var(--green);color:#fff;font-size:14px;line-height:44px;text-align:center;letter-spacing:.5px}
.rule{left:77px;width:550px;height:1px;background:var(--line)}
.partners{left:77px;top:1060px;width:551px;height:58px;border:1px solid var(--card-border);display:flex}
.partners div{flex:1;border-right:1px solid var(--card-border);display:flex;align-items:center;justify-content:center;gap:4px;font-size:8px;color:#666}
.partners div:last-child{border-right:0}
.partners div.on{background:var(--panel);color:var(--green)}
.partners i{width:8px;height:8px;border-radius:50%;background:currentColor;display:block}
.footer{left:0;top:1138px;width:704px;height:62px;background:var(--green);color:#fff}
.footer .links{left:77px;top:20px;font-size:7px;letter-spacing:.1px}
.footer .copy{left:77px;top:42px;font-size:6.5px}
.footer .share{left:507px;top:24px;font-size:7.5px;display:flex;align-items:center;gap:4px}
.footer .share i{width:7px;height:7px;border-radius:50%;background:#fff;display:block}
.footer .mark{left:661px;top:40px;font-size:6.5px}
</style>
</head>
<body>
<div class="abs topline"></div>
<header>
  <div class="abs brand"><span class="brand-mark"></span><span class="brand-name">Dunmore Kestrel</span></div>
  <div class="abs call">Call Us:<b>917-555-0183</b></div>
</header>
<nav class="abs nav"><ul><li>ABOUT US</li><li>SERVICES</li><li>REPRESENTATIVE ENGAGEMENTS</li><li>GLOBAL SCOPE AND PERSPECTIVE</li><li>BIOS</li></ul></nav>

<section class="abs hero" role="img" aria-label="Upward view of modern glass office towers and construction cranes against a blue sky"></section>
<div class="abs quote">"One of the World's Premier Investment Banks<br>to the Steel, Metals, and Mining Industries"</div>

<div class="abs card" style="left:77px">
  <h3>Team Support</h3>
  <svg width="50" height="50" viewBox="0 0 50 50"><circle cx="25" cy="25" r="25" fill="#5a5a5a"/><rect x="12" y="16" width="26" height="18" rx="2" fill="#fff"/><path d="M12 18l13 10 13-10" stroke="#5a5a5a" stroke-width="3" fill="none"/></svg>
  <p>We are international in scope, re presenting companies all around the world. This gives us a true</p>
  <a>» Read More</a>
</div>
<div class="abs card" style="left:220px">
  <h3>Strategic Advice</h3>
  <svg width="50" height="50" viewBox="0 0 50 50"><path d="M18 16v-4a7 7 0 0 1 14 0v4" stroke="#5a5a5a" stroke-width="3" fill="none"/><path d="M12 16h26v32H12z" fill="#5a5a5a"/><path d="M20 24l7 0 4 5-4 5-7 0z" fill="#fff"/></svg>
  <p>We are international in scope, re presenting companies all around the world. This gives us a true</p>
  <a>» Read More</a>
</div>
<div class="abs card" style="left:360px">
  <h3>Mergers &amp; Acquisitions</h3>
  <svg width="50" height="50" viewBox="0 0 50 50"><g fill="#5a5a5a"><circle cx="25" cy="25" r="16"/><rect x="21" y="2" width="8" height="46"/><rect x="2" y="21" width="46" height="8"/><rect x="21" y="2" width="8" height="46" transform="rotate(45 25 25)"/><rect x="21" y="2" width="8" height="46" transform="rotate(-45 25 25)"/></g><circle cx="25" cy="25" r="7" fill="#fff"/></svg>
  <p>We are international in scope, re presenting companies all around the world. This gives us a true</p>
  <a>» Read More</a>
</div>
<div class="abs card" style="left:500px">
  <h3>Capital Raising</h3>
  <svg width="50" height="50" viewBox="0 0 50 50"><g fill="#5a5a5a"><rect x="7" y="30" width="9" height="16"/><rect x="20" y="20" width="9" height="26"/><rect x="33" y="6" width="9" height="40"/></g></svg>
  <p>We are international in scope, re presenting companies all around the world. This gives us a true</p>
  <a>» Read More</a>
</div>

<section class="abs about" style="left:77px;top:561px;width:356px">
  <h2 class="heading">About Us</h2>
  <p>But I must explain to you how all this mistaken idea of denouncing pleasure and praising psdaif the system n was born and I will give you a complete account of the system, and expound the actual f tfrgfhe systkemt chings of the great explorer of the truth, the master-builder of human happiness. No one ref the system'fger ects, dislikes, or avoids pleasure itself,</p>
  <p>it is pleasure, but because those who do not ationally encounter consequences tlorwgncgzfzxcbzationally en know how to pursue pleasure rationally encounter consequences tlorwgncgzfzxcbzhat are extremely painful Nor again is there anyone who loves or pursues or desires to obtain pain of itself, because it</p>
</section>

<section>
  <h2 class="abs heading" style="left:461px;top:561px;width:166px">Testimonials<span class="arrows"><span>‹</span><span>›</span></span></h2>
  <div class="abs testi-box">"Sed ut perspiciatis unde omnis iste natu error sit voluptatem accusantium dolore mque laudantium, totam"</div>
  <div class="abs testi-person"><b>Arthur P. Dunmore</b><span>Chief Executive Officer</span></div>
  <div class="abs portrait" role="img" aria-label="Portrait photo of the chief executive"></div>
</section>

<h2 class="abs heading" style="left:77px;top:725px;width:550px">Recent Blog Posts<span class="arrows"><span>‹</span><span>›</span></span></h2>
<article class="abs post" style="left:77px">
  <div class="photo" role="img" aria-label="Bank building facade with reflective glass tower" style="background:linear-gradient(135deg,#3d4a3c,#8fa08c 55%,#2e3a30)"></div>
  <div class="abs date">Apr<b>13</b></div><div class="abs media"></div>
  <h4>Neque porro quisquam est qui.</h4><p>There is no one who by admin, 9 comments</p>
</article>
<article class="abs post" style="left:266px">
  <div class="photo" role="img" aria-label="Brick power plant with smokestacks by the water" style="background:linear-gradient(180deg,#6f9bd0,#a9c3e0 45%,#7a4a36 75%,#4d4a48)"></div>
  <div class="abs date">Apr<b>13</b></div><div class="abs media"></div>
  <h4>Neque porro quisquam est qui.</h4><p>There is no one who by admin, 9 comments</p>
</article>
<article class="abs post" style="left:454px">
  <div class="photo" role="img" aria-label="Busy industrial trade fair hall with exhibition stands" style="background:linear-gradient(180deg,#b8b6c6,#c9a86a 50%,#a8342c)"></div>
  <div class="abs date">Apr<b>13</b></div><div class="abs media"></div>
  <h4>Neque porro quisquam est qui.</h4><p>There is no one who by admin, 9 comments</p>
</article>

<div class="abs rule" style="top:950px"></div>
<div class="abs banner">Broker Dealer Related Services Provided Through Orvanne Partners LLC</div>
<div class="abs rule" style="top:1001px"></div>

<h2 class="abs heading" style="left:77px;top:1028px;width:550px">Affiliate of Orvanne<span class="arrows"><span>‹</span><span>›</span></span></h2>
<div class="abs partners">
  <div><i></i>Ashvale</div>
  <div class="on"><i></i>Brightfold</div>
  <div><i></i>Corwin Labs</div>
  <div><i></i>Delmora</div>
  <div><i></i>Elstone</div>
</div>

<footer class="abs footer">
  <div class="abs links">ABOUT US &nbsp;|&nbsp; SERVICES &nbsp;|&nbsp; REPRESENTATIVE ENGAGEMENTS &nbsp;|&nbsp; GLOBAL SCOPE AND PERSPECTIVE &nbsp;|&nbsp; BIOS</div>
  <div class="abs copy">© 2014 Northpine Studio all copyrights are reseved , 410 Harlow Avenue, 12th Floor, New York, NY 10022 &nbsp;Tel. 212.555.0147</div>
  <div class="abs share">Share Me:&nbsp;<i></i><i></i><i></i><i></i><i></i><i></i></div>
  <div class="abs mark">C4</div>
</footer>
</body>
</html>
```